New Innovative Counselling and psychotherapy Service needs Business Card design

Keep it simple and professional. On one side, just company name and logo (perhaps in all blue) and maybe a tag line.

On other side (all white) my name and Qualifications in centre

Industry/Entity Type

Health And Wellness

Contact Information for Business Card

Dara Whelby
Counsellor & Psychotherapist
BSc (Psychol.), BA, Dip. (Couns. & Psych.), PG.Cert (CBT), FGTrK, ONRE

I will also require Mobile no, Email and web site address of which I'll pass on to final designer.

Font styles to use
Sans Serif

Requirements
Must have
• My Logo Only and please use the colours in logo that is in it.
Should not have
• Any other images

```html
<!DOCTYPE html>
<html lang="en">
<head>
<meta charset="UTF-8">
<title>Tenderfield – Business Card</title>
<link href="https://fonts.googleapis.com/css2?family=Work+Sans:wght@300;400;500&display=swap" rel="stylesheet">
<style>
  :root {
    --backdrop: #1a1a1a;
    --card: #1e1e1e;
    --card-edge: #262626;
    --emboss: #2f2f2f;
    --emboss-light: #383838;
    --foil: #cfcfcf;
    --foil-soft: #b9b9b9;
    --divider: #5a5a5a;
  }
  * { margin: 0; padding: 0; box-sizing: border-box; }
  html, body {
    width: 1200px; height: 900px; overflow: hidden;
    background: var(--backdrop);
    font-family: "Work Sans", sans-serif;
  }
  .canvas {
    position: relative; width: 1200px; height: 900px;
    display: flex; flex-direction: column; align-items: center; justify-content: center; gap: 36px;
  }
  .card {
    position: relative; width: 700px; height: 400px;
    background: linear-gradient(135deg, var(--card-edge), var(--card) 60%);
    border-radius: 4px;
    box-shadow: 0 10px 30px rgba(0,0,0,.45);
  }
  /* front */
  .card-front { display: flex; flex-direction: column; align-items: center; justify-content: center; }
  .brand { display: flex; align-items: center; gap: 22px; }
  .brand-dot {
    width: 76px; height: 76px; border-radius: 50%;
    background: var(--emboss);
  }
  .brand-name {
    font-weight: 300; font-size: 46px; letter-spacing: .5px;
    color: var(--emboss-light);
  }
  .card-front .web {
    position: absolute; bottom: 34px; left: 0; right: 0; text-align: center;
    font-size: 17px; letter-spacing: 1px; color: var(--emboss-light);
  }
  /* back */
  .card-back { display: flex; align-items: center; }
  .card-back .brand { width: 345px; justify-content: center; gap: 16px; }
  .card-back .brand-dot { width: 56px; height: 56px; }
  .card-back .brand-name { font-size: 32px; }
  .divider {
    width: 2px; height: 210px; background: var(--divider);
  }
  .details { padding-left: 26px; color: var(--foil); }
  .person-name {
    font-weight: 500; font-size: 34px; letter-spacing: 1.5px; text-transform: uppercase;
    margin-bottom: 6px;
  }
  .role, .qualifications {
    font-size: 17px; line-height: 1.2; letter-spacing: .6px; color: var(--foil-soft);
  }
  .qualifications { width: 300px; margin-bottom: 16px; }
  .contact { list-style: none; }
  .contact li {
    display: flex; align-items: center; gap: 12px;
    font-size: 18px; letter-spacing: .8px; line-height: 1.55;
  }
  .contact svg { width: 12px; height: 12px; flex: none; }
</style>
</head>
<body>
<main class="canvas">
  <section class="card card-front">
    <div class="brand">
      <span class="brand-dot"></span>
      <span class="brand-name">Tenderfield</span>
    </div>
    <p class="web">www.tenderfieldcare.com</p>
  </section>

  <section class="card card-back">
    <div class="brand">
      <span class="brand-dot"></span>
      <span class="brand-name">Tenderfield</span>
    </div>
    <span class="divider"></span>
    <div class="details">
      <h1 class="person-name">Dara Whelby</h1>
      <p class="role">Counsellor &amp; Psychotherapist</p>
      <p class="qualifications">BSc (Psychol.), BA, Dip. (Couns. &amp; Psych.), PG.Cert (CBT), FGTrK, ONRE</p>
      <ul class="contact">
        <li>
          <svg viewBox="0 0 12 12" aria-hidden="true"><path d="M2.5 1 4.5 1 5.3 3.5 4 4.5Q5 7 7.5 8L8.5 6.7 11 7.5 11 9.5Q10.5 11 9 11 1 10 1 3 1 1.5 2.5 1Z" fill="var(--foil)"/></svg>
          555-014-2290
        </li>
        <li>
          <svg viewBox="0 0 12 12" aria-hidden="true"><rect x="1" y="2.5" width="10" height="7" fill="none" stroke="var(--foil)" stroke-width="1.2"/><path d="M1 2.5 6 6.5 11 2.5" fill="none" stroke="var(--foil)" stroke-width="1.2"/></svg>
          info@tenderfieldcare.com
        </li>
        <li>
          <svg viewBox="0 0 12 12" aria-hidden="true"><circle cx="6" cy="6" r="5" fill="none" stroke="var(--foil)" stroke-width="1.1"/><ellipse cx="6" cy="6" rx="2.2" ry="5" fill="none" stroke="var(--foil)" stroke-width="1"/><path d="M1 6H11" stroke="var(--foil)" stroke-width="1"/></svg>
          www.tenderfieldcare.com
        </li>
      </ul>
    </div>
  </section>
</main>
</body>
</html>
```